Spiritual Healing bussiness needs logo/business card

Simple, clean looking logo/card
For spiritual business with healing services and occult rituals

Contact Information for Business Card

Needs my name: Tobin Varley
Business name: Lantern Healing Shop
Services provided and worded in this way:

Reiki Healing
Tarot
Oils
Rituals Of Change

Can look occult like but with light energy.

Colors
0255a3
3276b5
85abd2
33a6d7
85cae6
0292cd

```html
<!DOCTYPE html>
<html lang="en">
<head>
<meta charset="utf-8">
<title>Tobin Varley – Lantern Healing Shop</title>
<link rel="stylesheet" href="https://fonts.googleapis.com/css2?family=Cookie&family=Montserrat:wght@500;600&display=swap">
<style>
  :root {
    --card-blue: #4472b7;
    --mint: #74c39b;
    --white: #ffffff;
  }
  html, body {
    margin: 0;
    padding: 0;
    overflow: hidden;
    background: var(--card-blue);
  }
  .card {
    position: relative;
    width: 1200px;
    height: 777px;
    background: var(--card-blue);
    overflow: hidden;
  }
  .brand {
    position: absolute;
    left: 42px;
    top: 42px;
    display: flex;
    align-items: center;
    gap: 16px;
  }
  .brand-mark {
    width: 34px;
    height: 34px;
    background: var(--mint);
  }
  .brand-name {
    font-family: "Montserrat", sans-serif;
    font-weight: 600;
    font-size: 30px;
    letter-spacing: 0.04em;
    color: var(--mint);
  }
  .services {
    position: absolute;
    right: 44px;
    top: 78px;
    margin: 0;
    padding: 0;
    list-style: none;
    text-align: right;
    font-family: "Cookie", cursive;
    font-size: 62px;
    line-height: 84px;
    color: var(--white);
  }
  .owner-name {
    position: absolute;
    right: 40px;
    top: 585px;
    margin: 0;
    font-family: "Montserrat", sans-serif;
    font-weight: 600;
    font-size: 104px;
    line-height: 1;
    letter-spacing: 0.01em;
    color: var(--mint);
    white-space: nowrap;
  }
</style>
</head>
<body>
  <main class="card">
    <div class="brand">
      <span class="brand-mark"></span>
      <span class="brand-name">Lantern Healing Shop</span>
    </div>
    <ul class="services">
      <li>Reiki Healing</li>
      <li>Tarot</li>
      <li>Oils</li>
      <li>Rituals Of Change</li>
    </ul>
    <h1 class="owner-name">TOBIN VARLEY</h1>
  </main>
</body>
</html>
```